Redesign and move to Wordpress for corvandel.com

Our website needs a redesign and at the same time we are moving it to Wordpress. Please help us with a new digital professional look and feel.

We are an Australian Software Engineering company specialising in advanced software development using in A.I., PLatform Engineering, Integration and Cloud. See the current corvandel.com for more information about us.

```html
<!DOCTYPE html>
<html lang="en">
<head>
<meta charset="utf-8">
<title>Corvandel — Reliable Smart Software Engineering</title>
<link href="https://fonts.googleapis.com/css2?family=Orbitron:wght@600;700&family=Roboto:wght@400;500;700&display=swap" rel="stylesheet">
<style>
:root{
  --navy:#061a2e;
  --navy-2:#0a2440;
  --blue:#1e5fa8;
  --teal:#4ec0b8;
  --teal-dark:#2e8f8a;
  --white:#ffffff;
  --muted:#c9d6e3;
  --link:#3f8fd6;
}
*{margin:0;padding:0;box-sizing:border-box}
html,body{width:1200px;height:3394px;overflow:hidden;background:var(--navy)}
body{font-family:'Roboto',Arial,sans-serif;color:var(--white);position:relative}
.abs{position:absolute}
.display{font-family:'Orbitron',sans-serif;font-weight:700;letter-spacing:4px;text-transform:uppercase}
.btn{position:absolute;border:2px solid var(--teal);color:var(--white);font-size:14px;font-weight:700;display:flex;align-items:center;justify-content:center;text-transform:uppercase;background:transparent}

/* hero */
.hero{position:absolute;left:0;top:0;width:1200px;height:621px;background:linear-gradient(120deg,#0b2a5c 0%,#0f4a8a 55%,#1a6fb0 100%)}
.hero-art{position:absolute;left:0;top:110px;width:560px;height:500px;background:radial-gradient(ellipse at 45% 40%,#2a7fd0 0%,#124b8a 45%,rgba(11,42,92,0) 75%)}
.hero-chart{position:absolute;left:800px;top:300px;width:400px;height:321px;background:linear-gradient(180deg,rgba(70,150,220,0) 0%,rgba(70,150,220,.35) 100%)}
.logo{position:absolute;left:143px;top:44px;display:flex;align-items:center;gap:14px}
.logo-mark{width:40px;height:40px;border:3px solid var(--white)}
.logo-name{font-size:30px;font-weight:400;letter-spacing:2px}
.nav{position:absolute;top:58px;left:561px;display:flex;gap:36px;font-size:15px;font-weight:700}
.nav .active{border-bottom:2px solid var(--teal);padding-bottom:6px}
.hero-title{position:absolute;left:506px;top:245px;font-size:36px;line-height:44px}
.dots{position:absolute;left:570px;top:540px;display:flex;gap:14px}
.dots span{width:9px;height:9px;border-radius:50%;background:var(--white)}
.dots span.on{background:var(--teal)}

/* welcome */
.photo{position:absolute;border:2px solid var(--teal);background:linear-gradient(160deg,#1f8f8a,#0a3a5a)}
.welcome-text{position:absolute;left:614px;top:795px;width:442px;font-size:14.5px;line-height:23px;text-align:justify;color:var(--muted)}

/* services */
.frame-outer{position:absolute;left:0;top:1128px;width:1200px;height:809px;border:2px solid var(--teal)}
.frame-inner{position:absolute;left:29px;top:1155px;width:1143px;height:753px;border:2px solid var(--blue)}
.card{position:absolute;width:208px;border:4px solid var(--blue);background:var(--navy);text-align:center;padding:22px 12px 0}
.card.teal{border-color:var(--teal)}
.card.double{border:3px solid var(--teal);outline:3px solid var(--teal);outline-offset:5px}
.card h3{font-size:14px;font-weight:700;line-height:20px;margin:14px 0 8px;text-transform:uppercase}
.card p{font-size:11.5px;line-height:18.5px;color:var(--muted)}
.card .ico{width:26px;height:26px;margin:0 auto}
.card .more{position:absolute;left:50%;bottom:14px;transform:translateX(-50%)}

/* news */
.news{position:absolute;top:2165px;width:290px;height:308px;border:1px solid #3a5a7a;padding:120px 29px 0}
.news.featured{border:3px solid var(--blue)}
.news-img{position:absolute;left:29px;top:-40px;width:231px;height:140px}
.news h4{font-size:14px;font-weight:700;margin-bottom:12px}
.news .sub{font-size:11.5px;line-height:18px;color:var(--link);margin-bottom:10px}
.news p{font-size:11.5px;line-height:18.5px;color:var(--muted)}
.news .rm{position:absolute;left:29px;bottom:20px;font-size:11.5px;color:var(--link)}
.arrow{position:absolute;top:2303px;width:44px;height:44px;border:1.5px solid #8aa0b8;border-radius:50%}

/* subscribe */
.sub-outer{position:absolute;left:0;top:2645px;width:1200px;height:405px;border:2px solid var(--teal)}
.sub-inner{position:absolute;left:30px;top:2675px;width:1140px;height:343px;background:linear-gradient(180deg,#4ec0b8 0%,#2a8cb0 45%,#1c5fa8 100%)}
.input{position:absolute;left:347px;top:2895px;width:345px;height:48px;background:var(--white);color:#6b7785;font-size:13px;padding:0 18px;display:flex;align-items:center}

/* footer */
.foot-links{position:absolute;left:143px;top:3280px;display:flex;gap:36px;font-size:16px;font-weight:700}
.social{position:absolute;top:3281px;left:905px;display:flex;gap:12px;font-size:13px;font-weight:500}
.social span{display:flex;align-items:center;gap:5px}
.social i{width:12px;height:12px;border-radius:50%;background:var(--white);display:block}
</style>
</head>
<body>

<!-- HERO -->
<section class="hero">
  <div class="hero-chart" role="img" aria-label="Rising bar chart and growth curve illustration"></div>
  <div class="hero-art" role="img" aria-label="Illustration of a laptop with floating data panels and connected network nodes"></div>
  <div class="logo"><span class="logo-mark"></span><span class="logo-name">corvandel</span></div>
  <nav class="nav">
    <span class="active">HOME</span><span>SERVICES</span><span>ABOUT</span><span>BLOG</span><span>CONTACT</span>
    <svg width="16" height="16" viewBox="0 0 16 16" style="margin-left:8px"><circle cx="6.5" cy="6.5" r="5" fill="none" stroke="#fff" stroke-width="2"/><line x1="10" y1="10" x2="15" y2="15" stroke="#fff" stroke-width="2"/></svg>
  </nav>
  <h1 class="hero-title display">Reliable<br>Smart Software<br>Engineering</h1>
  <div class="btn" style="left:506px;top:395px;width:175px;height:57px;font-size:15px">Get Started</div>
  <div class="dots"><span></span><span></span><span class="on"></span></div>
</section>

<!-- WELCOME -->
<section>
  <div class="photo" style="left:143px;top:686px;width:195px;height:138px" role="img" aria-label="Code on screen with a hand gesturing"></div>
  <div class="photo" style="left:342px;top:686px;width:195px;height:218px" role="img" aria-label="Software engineer with glasses in front of data overlays"></div>
  <div class="photo" style="left:143px;top:828px;width:195px;height:217px" role="img" aria-label="Developer working at multiple monitors"></div>
  <div class="photo" style="left:342px;top:908px;width:195px;height:137px;background:linear-gradient(160deg,#1a5a9a,#0a2a4a)" role="img" aria-label="Hands typing on a glowing keyboard"></div>
  <h2 class="display abs" style="left:614px;top:737px;font-size:30px">Welcome</h2>
  <p class="welcome-text">At Corvandel, we craft bespoke software solutions that are not available on the market. By building organizations market-leading products, process automation, legacy system enablement, or advanced intelligent systems, we empower our customers to achieve a competitive edge in their industry.</p>
  <div class="btn" style="left:614px;top:942px;width:145px;height:48px">Read More</div>
</section>

<!-- SERVICES -->
<section>
  <div class="frame-outer"></div>
  <div class="frame-inner"></div>
  <h2 class="display abs" style="left:0;width:1200px;text-align:center;top:1230px;font-size:30px">Our Services</h2>

  <div class="card" style="left:145px;top:1311px;height:217px">
    <svg class="ico" viewBox="0 0 26 26" fill="#fff"><rect x="1" y="1" width="7" height="7"/><rect x="10" y="1" width="7" height="7"/><rect x="19" y="1" width="7" height="7"/><rect x="1" y="10" width="7" height="7"/><rect x="10" y="10" width="7" height="7"/><rect x="19" y="10" width="7" height="7"/><rect x="1" y="19" width="7" height="7"/><rect x="10" y="19" width="7" height="7"/><rect x="19" y="19" width="7" height="7"/></svg>
    <h3>Microservices</h3>
    <p>Leverage Microservices Architecture to enable quick deployment, dynamically</p>
    <svg class="more" width="22" height="22" viewBox="0 0 22 22"><circle cx="11" cy="11" r="9.5" fill="none" stroke="#fff" stroke-width="1.5"/><path d="M11 6v9M7 11l4 4 4-4" fill="none" stroke="#fff" stroke-width="1.5"/></svg>
  </div>

  <div class="card double" style="left:386px;top:1318px;height:263px;width:194px">
    <svg class="ico" viewBox="0 0 26 26"><circle cx="13" cy="13" r="8" fill="none" stroke="#fff" stroke-width="5" stroke-dasharray="4 2.3"/><circle cx="13" cy="13" r="6" fill="#fff"/><circle cx="13" cy="13" r="2.5" fill="#061a2e"/></svg>
    <h3>Enterprise<br>Systems<br>Integration</h3>
    <p>Automate your business processes internally or externally to improve</p>
    <svg class="more" width="22" height="22" viewBox="0 0 22 22"><circle cx="11" cy="11" r="9.5" fill="none" stroke="#fff" stroke-width="1.5"/><path d="M11 6v9M7 11l4 4 4-4" fill="none" stroke="#fff" stroke-width="1.5"/></svg>
  </div>

  <div class="card" style="left:612px;top:1311px;height:217px">
    <svg class="ico" viewBox="0 0 26 26" fill="#fff"><path d="M13 2 2 8h22z"/><rect x="4" y="10" width="3" height="10"/><rect x="9.5" y="10" width="3" height="10"/><rect x="14" y="10" width="3" height="10"/><rect x="19" y="10" width="3" height="10"/><rect x="2" y="21" width="22" height="3"/></svg>
    <h3>Platform Engineering</h3>
    <p>For organisations looking to manage the security and cost risks around their cloud</p>
    <svg class="more" width="22" height="22" viewBox="0 0 22 22"><circle cx="11" cy="11" r="9.5" fill="none" stroke="#fff" stroke-width="1.5"/><path d="M11 6v9M7 11l4 4 4-4" fill="none" stroke="#fff" stroke-width="1.5"/></svg>
  </div>

  <div class="card teal" style="left:846px;top:1311px;height:277px">
    <svg class="ico" viewBox="0 0 26 26" fill="#fff"><rect x="9" y="1" width="8" height="7"/><rect x="1" y="18" width="7" height="7"/><rect x="9.5" y="18" width="7" height="7"/><rect x="18" y="18" width="7" height="7"/><path d="M12 8h2v4h8v6h-2v-4h-6v4h-2v-4H6v4H4v-6h8z"/></svg>
    <h3>Conversational AI</h3>
    <p>Enabling legacy systems with conversational user interfaces, or simply building intelligent natural language based services, conversational AI has many use cases across sales and operations.</p>
  </div>

  <div class="card teal" style="left:145px;top:1551px;height:277px">
    <svg class="ico" viewBox="0 0 26 26" fill="#fff"><path d="M7 21a6 6 0 0 1-1-11.9A7 7 0 0 1 19 8a5 5 0 0 1 1 13z"/></svg>
    <h3>iPaaS</h3>
    <p>Integration Platform as a Service brings the power of cloud based services to traditional systems integration. This is the new integration approach that enables</p>
    <svg class="more" width="22" height="22" viewBox="0 0 22 22"><circle cx="11" cy="11" r="9.5" fill="none" stroke="#fff" stroke-width="1.5"/><path d="M11 6v9M7 11l4 4 4-4" fill="none" stroke="#fff" stroke-width="1.5"/></svg>
  </div>

  <div class="card" style="left:379px;top:1610px;height:218px">
    <svg class="ico" viewBox="0 0 26 26" fill="#fff"><ellipse cx="13" cy="5" rx="9" ry="3.5"/><path d="M4 8c0 2 4 3.5 9 3.5S22 10 22 8v4c0 2-4 3.5-9 3.5S4 14 4 12zM4 15c0 2 4 3.5 9 3.5s9-1.5 9-3.5v5c0 2-4 3.5-9 3.5S4 22 4 20z"/></svg>
    <h3>Pairmate / AI Agents</h3>
    <p>The future of business AI are autonomous agents that specialise in your business data and processes.</p>
    <svg class="more" width="22" height="22" viewBox="0 0 22 22"><circle cx="11" cy="11" r="9.5" fill="none" stroke="#fff" stroke-width="1.5"/><path d="M11 6v9M7 11l4 4 4-4" fill="none" stroke="#fff" stroke-width="1.5"/></svg>
  </div>

  <div class="card teal" style="left:612px;top:1551px;height:277px">
    <svg class="ico" viewBox="0 0 26 26" fill="#fff"><circle cx="13" cy="7" r="4"/><circle cx="5" cy="9" r="3"/><circle cx="21" cy="9" r="3"/><path d="M6 20c0-4 3-7 7-7s7 3 7 7zM0 19c0-3 2-5 5-5l2 .5A8 8 0 0 0 4.5 19zM26 19c0-3-2-5-5-5l-2 .5a8 8 0 0 1 2.5 4.5z"/></svg>
    <h3>Custom Integration for Small to Medium Business</h3>
    <p>Our expertise in platform engineering, iPaaS, building distributed systems and enterprise systems</p>
    <svg class="more" width="22" height="22" viewBox="0 0 22 22"><circle cx="11" cy="11" r="9.5" fill="none" stroke="#fff" stroke-width="1.5"/><path d="M11 6v9M7 11l4 4 4-4" fill="none" stroke="#fff" stroke-width="1.5"/></svg>
  </div>

  <div class="card" style="left:846px;top:1610px;height:218px">
    <svg class="ico" viewBox="0 0 26 26"><circle cx="13" cy="13" r="12" fill="#fff"/><path d="M13 6v7l4 3" fill="none" stroke="#061a2e" stroke-width="2.5"/></svg>
    <h3>Real-Time Data Stream Processing</h3>
    <p>Being able to react to changing business conditions in a precise intelligent</p>
    <svg class="more" width="22" height="22" viewBox="0 0 22 22"><circle cx="11" cy="11" r="9.5" fill="none" stroke="#fff" stroke-width="1.5"/><path d="M11 6v9M7 11l4 4 4-4" fill="none" stroke="#fff" stroke-width="1.5"/></svg>
  </div>
</section>

<!-- NEWS -->
<section>
  <h2 class="display abs" style="left:0;width:1200px;text-align:center;top:2025px;font-size:30px">News &amp; Articles</h2>
  <div class="arrow" style="left:72px"><svg width="44" height="44" viewBox="0 0 44 44"><path d="M25 14l-8 8 8 8" fill="none" stroke="#fff" stroke-width="2"/></svg></div>
  <div class="arrow" style="left:1083px"><svg width="44" height="44" viewBox="0 0 44 44"><path d="M19 14l8 8-8 8" fill="none" stroke="#fff" stroke-width="2"/></svg></div>

  <article class="news" style="left:145px">
    <div class="news-img" style="background:linear-gradient(135deg,#0e4a6a,#1a7f8a 50%,#3a2a1a)" role="img" aria-label="Human hand and robot hand reaching toward an AI chip"></div>
    <h4>AI IN SOFTWARE ENGINEERING</h4>
    <div class="sub">10 unexpected ways to use Codehub Pairmate</div>
    <p>(Codehub Blog) Codehub Pairmate is widely known for its code generation feature. Learn how the AI assistant's abilities can extend beyond just code generation.</p>
    <span class="rm">READ MORE</span>
  </article>

  <article class="news featured" style="left:455px">
    <div class="news-img" style="background:linear-gradient(180deg,#d87a6a,#5a4a8a 45%,#1a3a3a)" role="img" aria-label="City skyline at dusk"></div>
    <h4>INDUSTRY RESEARCH</h4>
    <div class="sub">PROMTA: A general-purpose framework for prompt optimization</div>
    <p>(Northgate Research) Large language models (LLMs) have revolutionized various tasks, but prompt engineering</p>
    <span class="rm">READ MORE</span>
  </article>

  <article class="news" style="left:765px">
    <div class="news-img" style="background:linear-gradient(135deg,#b8d8f0,#4a8ad0 55%,#1a4a8a)" role="img" aria-label="Hand holding a tablet with rising business charts"></div>
    <h4>BUSINESS INSIGHTS</h4>
    <div class="sub">How Storytelling Helps Data-driven Teams Succeed</div>
    <p>(Ashford School of Management) Winning leaders know that data alone isn't enough. It's the art of storytelling</p>
    <span class="rm">READ MORE</span>
  </article>

  <div class="btn" style="left:528px;top:2508px;width:144px;height:48px">Load More</div>
</section>

<!-- SUBSCRIBE -->
<section>
  <div class="sub-outer"></div>
  <div class="sub-inner"></div>
  <h2 class="display abs" style="left:0;width:1200px;text-align:center;top:2742px;font-size:30px">Subscribe</h2>
  <p class="abs" style="left:0;width:1200px;text-align:center;top:2814px;font-size:17px;line-height:28px">Australia's Largest health charity implements Corvandel API Msg Bus<br>Register to our newsletter to find out more.</p>
  <div class="input">Enter Email</div>
  <div class="btn" style="left:708px;top:2895px;width:144px;height:48px;background:#1c5fa8">Subscribe</div>
</section>

<!-- BOOK NOW -->
<section>
  <h2 class="display abs" style="left:190px;top:3090px;font-size:30px">Book Now</h2>
  <p class="abs" style="left:190px;top:3150px;font-size:17px">Book an obligation free consultation with our Lead Technologist</p>
  <div class="btn" style="left:863px;top:3125px;width:144px;height:48px">Book Now</div>
</section>

<!-- FOOTER -->
<footer>
  <div class="foot-links"><span>HOME</span><span>SERVICES</span><span>ABOUT</span><span>BLOG</span><span>CONTACT</span></div>
  <div class="social"><span><i></i>Kivo</span><span><i></i>Parla</span><span><i></i>Nexo</span></div>
  <p class="abs" style="left:143px;top:3328px;font-size:12.5px;color:var(--muted)">© 2025 corvandel.All Rights Reserved &nbsp;| &nbsp;Privacy Policy &nbsp;| &nbsp;Terms of use</p>
</footer>

</body>
</html>
```